TLK Electricial Contracting Services

Hi guys, after a design for my small electrical company, have logo design files to be incorporated into the layout, the basic concept is electrical contracting services for residential, commercial, industrial & data services, image is clean clear and strong,

Card format is to have a nice clean logo on front,with maybe the Residential – commercial – industrial - data, followed with licensed & insured, followed by contact details on backside of the card.

Target Market(s)

Residential, commercial, industrial sectors.

Industry/Entity Type

Electrical

Contact Information for Business Card

TLK logo,
Residential – commercial – industrial - data
REC: 61307
Email: tlk@vornamail.net.au
Phone: 0487 352 019

Requirements
Must have
• Clean & strong design.
Nice to have
• If possible, I would like the logo colours inverted so the text is orange and the background is black on the front of the card, then the backside of the card be the reverse colour
Should not have
• No Sparks, lightning bolts,

```html
<!DOCTYPE html>
<html lang="en">
<head>
<meta charset="utf-8">
<title>TLK Electrical – Business Card</title>
<link rel="stylesheet" href="https://fonts.googleapis.com/css2?family=Saira:wght@500;600;700&display=swap">
<style>
  :root {
    --stage: #e9e6e2;
    --orange: #f0852b;
    --orange-light: #f7a04d;
    --orange-deep: #e2741c;
    --black: #0b0b0b;
    --charcoal: #1c1c1c;
    --brown: #5b3a28;
    --brown-dark: #3e2619;
    --white: #ffffff;
    --ink: #111111;
    --icon: #9a9a9a;
  }
  * { margin: 0; padding: 0; box-sizing: border-box; }
  html, body {
    width: 1200px; height: 900px; overflow: hidden;
    background: var(--stage);
    font-family: "Saira", sans-serif;
  }
  .canvas { position: relative; width: 1200px; height: 900px; }

  .card {
    position: absolute; width: 630px; height: 360px; overflow: hidden;
    box-shadow: 0 10px 28px rgba(0,0,0,.18);
  }

  /* Front */
  .card-front { left: 120px; top: 70px; }
  .front-texture {
    position: absolute; inset: 0;
    background: linear-gradient(135deg, var(--orange-light) 0%, var(--orange) 50%, var(--orange-deep) 100%);
  }
  .front-content { position: absolute; left: 110px; top: 92px; }
  .brand-name { font-weight: 700; line-height: 1; }
  .front-content .brand-name { font-size: 76px; color: var(--ink); }
  .front-content .company {
    font-size: 27px; font-weight: 700; color: var(--ink); margin-top: 10px; letter-spacing: .5px;
  }
  .front-content .licence {
    font-size: 17px; font-weight: 700; color: var(--ink); margin-top: 8px; padding-left: 40px;
  }
  .front-content .services {
    font-size: 17px; font-weight: 600; color: var(--white); margin-top: 4px; letter-spacing: .5px;
  }

  /* Back */
  .card-back { left: 450px; top: 470px; background: var(--black); }
  .back-panel {
    position: absolute; inset: 0;
    background: linear-gradient(160deg, var(--charcoal) 0%, var(--black) 70%);
  }
  .back-texture {
    position: absolute; inset: 0;
    clip-path: polygon(80% 0, 100% 0, 100% 100%, 68% 100%);
    background: linear-gradient(135deg, var(--brown) 0%, var(--brown-dark) 100%);
  }
  .back-divider { position: absolute; inset: 0; width: 100%; height: 100%; }
  .back-edge { position: absolute; left: 0; top: 0; bottom: 0; width: 12px; background: var(--orange); }
  .back-content { position: absolute; left: 60px; top: 38px; }
  .back-content .brand-name { font-size: 64px; color: var(--orange); }
  .back-content .company {
    font-size: 24px; font-weight: 700; color: var(--white); margin-top: 8px; letter-spacing: .5px;
  }
  .person { margin-top: 34px; }
  .person-name { font-size: 28px; font-weight: 700; color: var(--orange); line-height: 1.1; }
  .person-role { font-size: 17px; font-weight: 600; color: var(--white); }
  .contact { margin-top: 24px; list-style: none; }
  .contact li {
    display: flex; align-items: center; gap: 16px;
    font-size: 21px; font-weight: 500; color: var(--orange); line-height: 1.35;
  }
  .contact svg { width: 16px; height: 16px; flex: none; }
</style>
</head>
<body>
<main class="canvas">

  <section class="card card-front" aria-label="Business card front">
    <div class="front-texture" role="img" aria-label="Orange tiled grid background pattern"></div>
    <div class="front-content">
      <p class="brand-name">TLK</p>
      <p class="company">Tarvik Lane Electrical</p>
      <p class="licence">licenced &amp; insured Residential</p>
      <p class="services">commercial – industrial – data REC: 61307</p>
    </div>
  </section>

  <section class="card card-back" aria-label="Business card back">
    <div class="back-panel"></div>
    <div class="back-texture" role="img" aria-label="Brown tiled grid background pattern"></div>
    <svg class="back-divider" viewBox="0 0 630 360" preserveAspectRatio="none" aria-hidden="true">
      <line x1="500" y1="0" x2="427" y2="360" stroke="#ffffff" stroke-width="8"/>
    </svg>
    <div class="back-edge"></div>
    <div class="back-content">
      <p class="brand-name">TLK</p>
      <p class="company">Tarvik Lane Electrical</p>
      <div class="person">
        <p class="person-name">Dale Ferris</p>
        <p class="person-role">Owner</p>
      </div>
      <ul class="contact">
        <li>
          <svg viewBox="0 0 16 16" aria-hidden="true"><path d="M4 1.5l2.4 2.8-1.3 1.7c.9 2 2.4 3.6 4.5 4.6l1.7-1.3 2.9 2.3-1.3 2.4C7.8 14 2 8.3 1.8 3.2z" fill="var(--icon)"/></svg>
          <span>0487 352 019</span>
        </li>
        <li>
          <svg viewBox="0 0 16 16" aria-hidden="true"><rect x="1" y="3.5" width="14" height="9.5" fill="none" stroke="var(--icon)" stroke-width="1.4"/><path d="M1.5 4l6.5 5 6.5-5" fill="none" stroke="var(--icon)" stroke-width="1.4"/></svg>
          <span>tlk@vornamail.net.au</span>
        </li>
      </ul>
    </div>
  </section>

</main>
</body>
</html>
```